Business Card Design

We need a business card designed for our new company. Prefer a black card with white logo & writing.

Contact Information for Business Card

Ted Galloway, address: 7-4812 Fernhollow Road, Abbotsford, BC, V3K 8R2, Office Phone: 604-712-3390, Cell: 604-947-2164, Email: ted@resinworkshub.ca

Colors

Designer to choose only greyscale colors for use in the design.

```html
<!DOCTYPE html>
<html lang="en">
<head>
<meta charset="utf-8">
<title>Resinworks Hub — Business Card</title>
<link href="https://fonts.googleapis.com/css2?family=Montserrat:wght@400;500;700;800&display=swap" rel="stylesheet">
<style>
  :root {
    --stage: #2b2b2b;
    --card: #262626;
    --card-back: #1f1f1f;
    --ink: #ffffff;
    --ink-soft: #d9d9d9;
    --gloss: #0e0e0e;
  }
  * { margin: 0; padding: 0; box-sizing: border-box; }
  html, body { width: 1200px; height: 1200px; overflow: hidden; }
  body {
    background: var(--stage);
    font-family: "Montserrat", sans-serif;
    color: var(--ink);
    position: relative;
  }
  .card {
    position: absolute;
    left: 150px;
    width: 900px;
    height: 514px;
    box-shadow: 0 10px 30px rgba(0,0,0,.45);
  }
  .card--front { top: 60px; background: var(--card); }
  .card--back { top: 626px; background: var(--card-back); }

  .brand {
    position: absolute;
    left: 70px; top: 58px;
    font-weight: 800;
    font-size: 34px;
    letter-spacing: 1px;
    line-height: 1.1;
    text-transform: uppercase;
    color: var(--ink);
  }
  .person { position: absolute; left: 70px; top: 190px; }
  .person__name { font-weight: 700; font-size: 27px; letter-spacing: .5px; }
  .person__role { font-size: 15px; color: var(--ink-soft); margin-top: 2px; }

  .contact {
    position: absolute; left: 70px; top: 290px;
    list-style: none;
  }
  .contact__item {
    display: flex; align-items: center; gap: 16px;
    font-size: 17px; font-weight: 500; height: 30px;
    letter-spacing: .3px;
  }
  .contact__icon { width: 16px; height: 16px; fill: var(--ink); }

  .mountain {
    position: absolute; right: 0; bottom: 0;
    width: 470px; height: 175px;
    background: linear-gradient(160deg, rgba(255,255,255,0) 35%, rgba(255,255,255,.18) 75%, rgba(255,255,255,.32));
  }
  .address {
    position: absolute; right: 70px; bottom: 50px;
    text-align: left; font-size: 17px; font-weight: 500; line-height: 1.35;
  }

  .back-brand {
    position: absolute; left: 0; right: 0; top: 50%;
    transform: translateY(-50%);
    text-align: center;
    font-weight: 800; font-size: 72px; letter-spacing: 2px;
    text-transform: uppercase;
    color: var(--gloss);
  }
</style>
</head>
<body>
  <section class="card card--front">
    <div class="brand">Resinworks Hub</div>
    <div class="person">
      <div class="person__name">Ted Galloway</div>
      <div class="person__role">owner</div>
    </div>
    <ul class="contact">
      <li class="contact__item">
        <svg class="contact__icon" viewBox="0 0 24 24"><path d="M6.6 10.8a15 15 0 0 0 6.6 6.6l2.2-2.2a1 1 0 0 1 1-.25 11.4 11.4 0 0 0 3.6.57 1 1 0 0 1 1 1V20a1 1 0 0 1-1 1A17 17 0 0 1 3 4a1 1 0 0 1 1-1h3.5a1 1 0 0 1 1 1c0 1.25.2 2.45.57 3.57a1 1 0 0 1-.25 1z"/></svg>
        604-712-3390
      </li>
      <li class="contact__item">
        <svg class="contact__icon" viewBox="0 0 24 24"><path d="M7 1h10a2 2 0 0 1 2 2v18a2 2 0 0 1-2 2H7a2 2 0 0 1-2-2V3a2 2 0 0 1 2-2zm0 3v14h10V4zm5 15.5a1 1 0 1 0 0 2 1 1 0 0 0 0-2z"/></svg>
        604-947-2164
      </li>
      <li class="contact__item">
        <svg class="contact__icon" viewBox="0 0 24 24"><path d="M2 5h20v14H2zm2 2v.5l8 5 8-5V7z"/></svg>
        ted@resinworkshub.ca
      </li>
      <li class="contact__item">
        <svg class="contact__icon" viewBox="0 0 24 24"><circle cx="12" cy="12" r="10"/></svg>
        www.resinworkshub.ca
      </li>
    </ul>
    <div class="mountain" role="img" aria-label="White mountain peak silhouette rising to the bottom-right corner"></div>
    <div class="address">7-4812 Fernhollow Road,<br>Abbotsford, BC, V3K 8R2</div>
  </section>

  <section class="card card--back">
    <div class="back-brand">Resinworks Hub</div>
  </section>
</body>
</html>
```